Cedar Brook Stables, LLC

Equestrian business card to promote equine retirement, farm sitting, short term board. Located in Aiken, SC.
Updates
Updated color schemes.
Contact Information for Business Card
Contact info, description of work.
Colors
0094D4
00A9DD
6FCCEA
C7EBF8
E9F6FB
59FF00
82FF00
B8FF75
E3FFCB
F4FFEA
F0912C
F2A743
F7CA91
FBE8D2
FDF5EE

```html
<!DOCTYPE html>
<html lang="en">
<head>
<meta charset="utf-8">
<title>Cedar Brook Stables, LLC – Business Card</title>
<link rel="stylesheet" href="https://fonts.googleapis.com/css2?family=Poppins:wght@400;500;600;700&display=swap">
<style>
  :root {
    --page-bg: #d4d4d4;
    --sun-yellow: #ffd640;
    --sun-orange: #ffb300;
    --field-green: #16900c;
    --field-green-dark: #0b7404;
    --field-green-light: #2aa81c;
    --ink: #262626;
    --paper-white: #ffffff;
    --card-shadow: rgba(0, 0, 0, 0.28);
  }
  * { box-sizing: border-box; margin: 0; padding: 0; }
  html, body {
    width: 1200px;
    height: 800px;
    overflow: hidden;
  }
  body {
    background: var(--page-bg);
    font-family: "Poppins", sans-serif;
    display: flex;
    align-items: center;
    justify-content: center;
    gap: 40px;
  }
  .card {
    position: relative;
    width: 540px;
    height: 309px;
    overflow: hidden;
    box-shadow: 0 14px 30px var(--card-shadow);
  }

  /* Front: contact side */
  .card--front {
    background: radial-gradient(circle at 30% 85%, var(--sun-orange) 0%, var(--sun-yellow) 45%);
  }
  .front__horse {
    position: absolute;
    left: 40px;
    bottom: 0;
    width: 230px;
    height: 235px;
    border-radius: 110px 110px 0 0;
    background: linear-gradient(180deg, #3a3a3a 0%, var(--ink) 100%);
  }
  .front__meadow {
    position: absolute;
    inset: 0;
    width: 100%;
    height: 100%;
  }
  .front__contact {
    position: absolute;
    top: 24px;
    right: 26px;
    text-align: right;
    color: var(--ink);
  }
  .contact__name {
    font-size: 17px;
    font-weight: 700;
    letter-spacing: 0.5px;
    line-height: 1.1;
  }
  .contact__role {
    font-size: 11.5px;
    font-weight: 400;
    margin-bottom: 14px;
  }
  .contact__list { list-style: none; }
  .contact__item {
    display: flex;
    justify-content: flex-end;
    align-items: flex-start;
    gap: 8px;
    font-size: 11.5px;
    line-height: 1.45;
  }
  .contact__item + .contact__item { margin-top: 2px; }
  .contact__item--address { margin-top: 10px !important; }
  .contact__icon {
    width: 12px;
    height: 12px;
    flex: none;
    margin-top: 3px;
    fill: var(--ink);
  }

  /* Back: brand side */
  .card--back {
    background: radial-gradient(circle at 50% 40%, var(--field-green-light) 0%, var(--field-green) 45%, var(--field-green-dark) 100%);
    border-bottom: 3px solid var(--sun-yellow);
    display: flex;
    flex-direction: column;
    align-items: center;
    justify-content: center;
    color: var(--paper-white);
  }
  .brand {
    display: flex;
    align-items: center;
    gap: 12px;
    margin-top: 10px;
  }
  .brand__mark {
    width: 34px;
    height: 34px;
    border-radius: 50%;
    background: var(--sun-yellow);
    flex: none;
  }
  .brand__name {
    font-size: 26px;
    font-weight: 600;
    letter-spacing: 1px;
    color: var(--paper-white);
  }
  .brand__rule {
    width: 360px;
    height: 3px;
    background: var(--paper-white);
    margin: 14px 0 0;
  }
  .services {
    position: absolute;
    bottom: 26px;
    left: 0;
    right: 0;
    text-align: center;
    font-size: 13px;
    font-weight: 500;
    letter-spacing: 0.8px;
  }
  .services__dot {
    display: inline-block;
    width: 7px;
    height: 7px;
    border-radius: 50%;
    background: var(--sun-yellow);
    margin: 0 8px;
    vertical-align: middle;
  }
</style>
</head>
<body>

  <section class="card card--front">
    <div class="front__horse" role="img" aria-label="Silhouette of a rearing horse against a rising sun"></div>
    <svg class="front__meadow" viewBox="0 0 540 309" preserveAspectRatio="none" role="img" aria-label="Green grassy meadow rising across the card">
      <polygon points="0,292 540,100 540,309 0,309" fill="var(--field-green)"/>
    </svg>

    <div class="front__contact">
      <p class="contact__name">DANIEL WHITAKER</p>
      <p class="contact__role">Managing Director</p>
      <ul class="contact__list">
        <li class="contact__item">803-555 014 276
          <svg class="contact__icon" viewBox="0 0 24 24"><path d="M6.6 10.8a15.1 15.1 0 0 0 6.6 6.6l2.2-2.2a1 1 0 0 1 1-.25 11.4 11.4 0 0 0 3.6.57 1 1 0 0 1 1 1V20a1 1 0 0 1-1 1A17 17 0 0 1 3 4a1 1 0 0 1 1-1h3.5a1 1 0 0 1 1 1c0 1.25.2 2.45.57 3.57a1 1 0 0 1-.25 1z"/></svg>
        </li>
        <li class="contact__item">hello@cedarbrookstables.com
          <svg class="contact__icon" viewBox="0 0 24 24"><path d="M2 5h20v14H2z M2 5l10 8 10-8" fill="none" stroke="var(--ink)" stroke-width="2.4"/></svg>
        </li>
        <li class="contact__item">www.cedarbrookstables.com
          <svg class="contact__icon" viewBox="0 0 24 24"><g fill="none" stroke="var(--ink)" stroke-width="2"><circle cx="12" cy="12" r="10"/><ellipse cx="12" cy="12" rx="4.5" ry="10"/><path d="M2 12h20"/></g></svg>
        </li>
        <li class="contact__item contact__item--address">118 Fox Run Lane<br>Aiken, SC 29801
          <svg class="contact__icon" viewBox="0 0 24 24"><path d="M12 2a7 7 0 0 0-7 7c0 5.2 7 13 7 13s7-7.8 7-13a7 7 0 0 0-7-7zm0 9.5A2.5 2.5 0 1 1 12 6.5a2.5 2.5 0 0 1 0 5z"/></svg>
        </li>
      </ul>
    </div>
  </section>

  <section class="card card--back">
    <div class="brand">
      <span class="brand__mark"></span>
      <span class="brand__name">CEDAR BROOK STABLES, LLC</span>
    </div>
    <div class="brand__rule"></div>
    <p class="services">SHORT TERM BOARD<span class="services__dot"></span>FARM SITTING<span class="services__dot"></span>EQUINE RETIREMENT</p>
  </section>

</body>
</html>
```